AI Discovery Workshop Presentation

We have a wireframe presentation with 43 slides (many with the same format) to be implemented in Powerpoint. We provide Corporate presentation in order to reuse template. Please, be creative and don't take the examples in the wireframe as literal. We also provide the following:
- Color palette
- lumacrest Logos
- Slide wireframe
- Flyer
- lumacrest Corporate Presentation. Please, use this as a general template.
You can find all the materials here:
https://files.brivoshare.net/folders/7QpZ2mTxR8vLkN4sYdW0aJe3Fu9HcBg?usp=sharing

```html
<!DOCTYPE html>
<html lang="en">
<head>
<meta charset="utf-8">
<title>AI Discovery Workshop – lumacrest</title>
<link href="https://fonts.googleapis.com/css2?family=Poppins:wght@400;500;600;700&display=swap" rel="stylesheet">
<style>
:root{
  --page:#f4f4f4;
  --navy:#0a1b30;
  --navy-deep:#061425;
  --navy-glow:#0d2c40;
  --teal:#15968a;
  --teal-light:#2bb3a4;
  --white:#ffffff;
  --pill:#f6f8f8;
  --ink:#0a1b30;
  --rust:#8b3c1c;
  --stone:#4f4a45;
  --sage:#5f8a56;
  --tan:#c98a4a;
  --forest:#2e5a36;
  --ai:#f9d82e;
  --ml:#2a45a3;
  --fm:#f5464f;
}
*{margin:0;padding:0;box-sizing:border-box}
html,body{width:1019px;height:1200px;overflow:hidden;background:var(--page)}
body{font-family:"Poppins",sans-serif;color:var(--white);position:relative}
.slide{position:absolute;width:427px;height:240px;overflow:hidden;
  background:radial-gradient(ellipse at 75% 90%,var(--navy-glow) 0%,var(--navy) 55%,var(--navy-deep) 100%)}
.col-a{left:58px}.col-b{left:533px}
.row-1{top:55px}.row-2{top:336px}.row-3{top:618px}.row-4{top:900px}
.slide-title{position:absolute;left:21px;top:8px;font-size:17px;font-weight:700;letter-spacing:.2px}
.title-rule{position:absolute;left:0;top:36px;width:50px;height:1px;background:var(--teal)}
.title-rule::after{content:"";position:absolute;right:-3px;top:-2.5px;width:6px;height:6px;border-radius:50%;background:var(--teal)}
.brand{position:absolute;right:22px;top:9px;display:flex;align-items:center;gap:4px;font-size:20px;font-weight:600;line-height:1}
.brand-mark{width:10px;height:10px;background:var(--teal)}
.footer{position:absolute;left:0;bottom:5px;width:427px;height:15px;background:var(--teal);border-radius:0 8px 8px 0;
  display:flex;justify-content:space-between;align-items:center;padding:0 21px;font-size:6.3px;font-weight:600}
.footer b{font-size:7.5px}
.btn{position:absolute;height:18px;padding:0 7px;background:var(--teal);font-size:6.5px;display:flex;align-items:center;gap:5px}
.photo{position:absolute}
/* cover */
.cover-frame{position:absolute;inset:7px;border:1px solid var(--teal)}
.cover-brand{position:absolute;left:21px;top:72px;font-size:18px;font-weight:600;display:flex;align-items:center;gap:4px}
.cover-title{position:absolute;left:21px;top:102px;font-size:29px;font-weight:700;line-height:33px}
.cover-ring{position:absolute;left:205px;top:91px;width:210px;height:210px;border-radius:50%;background:#0b2236}
.cover-photo{left:215px;top:101px;width:190px;height:190px;border-radius:50%;background:linear-gradient(160deg,#1f3b4a,#c9a24a 60%,#6e8fb0)}
.cover-mask{position:absolute;left:8px;right:8px;top:232px;bottom:0;background:var(--navy-deep)}
/* intro */
.pill{position:absolute;left:21px;width:178px;height:27px;border-radius:14px;background:var(--pill);color:var(--ink);
  font-size:8px;font-weight:500;display:flex;align-items:center;justify-content:space-between;padding:0 10px 0 18px}
.pill svg{width:12px;height:12px}
.intro-photo{left:230px;top:54px;width:175px;height:139px;border-radius:5px;background:linear-gradient(135deg,#c9c3b8,#8a6d55 50%,#e0d7cb)}
/* about workshop */
.lead{position:absolute;left:21px;top:48px;font-size:9.2px;line-height:1.4}
.lead strong{display:block;color:var(--teal-light);font-size:12.5px;font-weight:600}
.node-root{position:absolute;left:200px;top:78px;width:26px;height:26px;background:var(--teal)}
.tree{position:absolute;left:0;top:0}
.node{position:absolute;top:136px;width:26px;height:26px;border-radius:50%;background:var(--teal);border:1.5px solid #d8f1ee;display:flex;align-items:center;justify-content:center}
.node-label{position:absolute;top:170px;width:120px;text-align:center;font-size:7.4px;font-weight:600}
/* agent */
.stage{position:absolute;top:75px;width:92px;height:92px;border-radius:50%;border:3px solid var(--teal);
  display:flex;align-items:center;justify-content:center;text-align:center;font-size:9px;font-weight:600;line-height:1.45}
.stage.is-first{background:var(--teal);box-shadow:0 0 0 3px var(--navy),0 0 0 5px var(--teal)}
/* ml */
.ml-back{position:absolute;left:32px;top:66px;width:168px;height:128px;background:var(--teal);clip-path:polygon(0 0,100% 0,100% 8%,8% 8%,8% 100%,0 92%)}
.ml-photo{left:41px;top:73px;width:159px;height:126px;background:linear-gradient(135deg,#0b2a6e,#1c7fd6 55%,#56d0f5)}
.body-copy{position:absolute;font-size:9px;line-height:15.3px}
/* examples */
.tile{position:absolute;width:116px;height:67px;padding:8px 10px;font-size:8.3px;font-weight:600;line-height:1.35}
.tile .glyph{position:absolute;right:10px;bottom:10px;width:34px;height:30px;border-radius:3px;background:rgba(255,255,255,.22)}
.tile-tall{height:142px;text-align:center}
.tile-tall .glyph{left:32px;right:auto;bottom:26px;width:52px;height:46px;border-radius:50%}
/* about us */
.tagline{position:absolute;left:0;right:0;top:55px;text-align:center;color:var(--teal-light);font-size:16.5px;font-weight:600;line-height:22px}
.centered{position:absolute;left:40px;right:40px;top:105px;text-align:center;font-size:9px;line-height:15px}
/* foundational */
.bar{position:absolute;bottom:55px;width:44px;display:flex;justify-content:center;font-weight:600;font-size:16.5px}
.bar-ai{left:33px;height:59px;background:var(--ai);color:var(--ink);align-items:center}
.bar-ml{left:87px;height:86px;background:var(--ml);padding-top:20px}
.bar-fm{left:142px;height:121px;background:var(--fm);padding-top:26px}
</style>
</head>
<body>

<section class="slide col-a row-1">
  <div class="cover-ring"></div>
  <div class="photo cover-photo" role="img" aria-label="Photo of two students building electronics together at a workbench"></div>
  <div class="cover-mask"></div>
  <div class="cover-frame"></div>
  <div class="cover-brand"><span class="brand-mark"></span>lumacrest</div>
  <h1 class="cover-title">AI Discovery<br>Workshop</h1>
  <div class="btn" style="left:21px;top:180px">Learn More <span>→</span></div>
</section>

<section class="slide col-b row-1">
  <h2 class="slide-title">INTRODUCTIONS</h2><div class="title-rule"></div>
  <div class="brand"><span class="brand-mark"></span>lumacrest</div>
  <div class="pill" style="top:52px">NAME<svg viewBox="0 0 12 12"><circle cx="6" cy="3.5" r="2.6" fill="#15968a"/><path d="M1.5 12a4.5 4.5 0 0 1 9 0z" fill="#15968a"/></svg></div>
  <div class="pill" style="top:91px">DEPARTMENT<svg viewBox="0 0 12 12"><path d="M6 1l5 2.5-5 2.5-5-2.5z M1 6l5 2.5 5-2.5 M1 8.5l5 2.5 5-2.5" fill="none" stroke="#15968a" stroke-width="1.3"/></svg></div>
  <div class="pill" style="top:130px">ROI<svg viewBox="0 0 12 12"><circle cx="6" cy="6" r="5" fill="none" stroke="#15968a" stroke-width="1.2"/><text x="6" y="8.3" font-size="6.5" text-anchor="middle" fill="#15968a" font-family="Poppins,sans-serif" font-weight="700">$</text></svg></div>
  <div class="pill" style="top:169px">WORKSHOP EXPECTATIONS<svg viewBox="0 0 12 12"><circle cx="6" cy="6" r="2.6" fill="#15968a"/><g stroke="#15968a" stroke-width="1.4"><path d="M6 .5v2.3M6 9.2v2.3M.5 6h2.3M9.2 6h2.3M2.1 2.1l1.6 1.6M8.3 8.3l1.6 1.6M2.1 9.9l1.6-1.6M8.3 3.7l1.6-1.6"/></g></svg></div>
  <div class="photo intro-photo" role="img" aria-label="Photo of three students working with a multimeter and tablet"></div>
  <footer class="footer"><span>Copyrights@2025.Company Name.All Rights Reserved</span><span>Page Number: <b>02</b></span></footer>
</section>

<section class="slide col-a row-2">
  <h2 class="slide-title">ABOUT THE WORKSHOP</h2><div class="title-rule"></div>
  <div class="brand"><span class="brand-mark"></span>lumacrest</div>
  <p class="lead">The objective of this workshop is for you to discover feasible and high-impact<strong>AI use cases.</strong></p>
  <div class="node-root"></div>
  <svg class="tree" width="427" height="240"><g fill="none" stroke="#cfd8dc" stroke-width=".8" stroke-dasharray="1.5 1.5"><path d="M213 104V136M77 136V118H347V136"/></g></svg>
  <div class="node" style="left:64px"><svg width="12" height="12" viewBox="0 0 12 12"><circle cx="6" cy="2.5" r="2" fill="#fff"/><path d="M4 5h4v4H4zM2 11h8" stroke="#fff" fill="#fff" stroke-width="1"/></svg></div>
  <div class="node" style="left:200px"><svg width="12" height="12" viewBox="0 0 12 12"><circle cx="6" cy="6" r="4.5" fill="none" stroke="#fff" stroke-width="1.4" stroke-dasharray="2 1.3"/><circle cx="6" cy="6" r="1.8" fill="#fff"/></svg></div>
  <div class="node" style="left:334px"><svg width="12" height="12" viewBox="0 0 12 12"><circle cx="3" cy="3.5" r="1.6" fill="#fff"/><circle cx="9" cy="3.5" r="1.6" fill="#fff"/><circle cx="6" cy="6.5" r="1.8" fill="#fff"/><path d="M2 11a4 3 0 0 1 8 0z" fill="#fff"/></svg></div>
  <div class="node-label" style="left:17px">You, not us</div>
  <div class="node-label" style="left:153px">Feasible, not impossible</div>
  <div class="node-label" style="left:287px">High impact</div>
  <footer class="footer"><span>Copyrights@2025.Company Name.All Rights Reserved</span><span>Page Number: <b>03</b></span></footer>
</section>

<section class="slide col-b row-2">
  <h2 class="slide-title">AGENT</h2><div class="title-rule"></div>
  <div class="brand"><span class="brand-mark"></span>lumacrest</div>
  <div class="stage is-first" style="left:23px">INSPIRE<br>(60 MINUTES)</div>
  <div class="stage" style="left:168px">DISCOVER<br>(60 MINUTES)</div>
  <div class="stage" style="left:312px">PRIORITIZE<br>(90 MINUTES)</div>
  <svg class="tree" width="427" height="240"><g stroke="#fff" stroke-width="1.2" fill="#fff"><path d="M118 121H160M263 121H305"/><path d="M166 121l-8-5v10zM311 121l-8-5v10z"/></g></svg>
  <footer class="footer"><span>Copyrights@2025.Company Name.All Rights Reserved</span><span>Page Number: <b>04</b></span></footer>
</section>

<section class="slide col-a row-3">
  <h2 class="slide-title">MACHINE LEARNING</h2><div class="title-rule"></div>
  <div class="brand"><span class="brand-mark"></span>lumacrest</div>
  <div class="ml-back"></div>
  <div class="photo ml-photo" role="img" aria-label="Illustration of a hand reaching toward a glowing machine learning circuit chip"></div>
  <p class="body-copy" style="left:229px;top:89px;width:180px">Machine learning is a subfield of artificial intelligence that focuses on enabling machines to learn from data using algorithms without being explicitly programmed for each task"</p>
  <footer class="footer"><span>Copyrights@2025.Company Name.All Rights Reserved</span><span>Page Number: <b>05</b></span></footer>
</section>

<section class="slide col-b row-3">
  <h2 class="slide-title">ML EXAMPLES</h2><div class="title-rule"></div>
  <div class="brand"><span class="brand-mark"></span>lumacrest</div>
  <div class="tile" style="left:35px;top:54px;background:var(--rust)">Demand<br>Prediction<div class="glyph" role="img" aria-label="Laptop with sales chart icon"></div></div>
  <div class="tile tile-tall" style="left:158px;top:54px;background:var(--stone)">Customer<br>Segmentation<div class="glyph" role="img" aria-label="Pie chart with customer figure icon"></div></div>
  <div class="tile" style="left:280px;top:54px;background:var(--sage)">Fraud<br>detection<div class="glyph" role="img" aria-label="Card with warning and magnifier icon"></div></div>
  <div class="tile" style="left:35px;top:129px;background:var(--tan)">Recommendation<br>Engine<div class="glyph" role="img" aria-label="Browser window icon"></div></div>
  <div class="tile" style="left:280px;top:129px;background:var(--forest)">Employee<br>attrition/<br>churn<div class="glyph" role="img" aria-label="Team held in hand icon"></div></div>
  <footer class="footer"><span>Copyrights@2025.Company Name.All Rights Reserved</span><span>Page Number: <b>06</b></span></footer>
</section>

<section class="slide col-a row-4">
  <h2 class="slide-title">ABOUT US</h2><div class="title-rule"></div>
  <div class="brand"><span class="brand-mark"></span>lumacrest</div>
  <p class="tagline">DATA ANALYTICS<br>&amp; AL FOR NONCONFORMISTS</p>
  <p class="centered">We are a leading Professional Services company specialized in the design and implementation of cutting edge technologies in Cloud Data Analytics &amp; AI.</p>
  <div class="btn" style="left:182px;top:160px">Learn More <span>→</span></div>
  <footer class="footer"><span>Copyrights@2025.Company Name.All Rights Reserved</span><span>Page Number: <b>07</b></span></footer>
</section>

<section class="slide col-b row-4">
  <h2 class="slide-title">FOUNDATIONAL MODELS</h2><div class="title-rule"></div>
  <div class="brand"><span class="brand-mark"></span>lumacrest</div>
  <div class="bar bar-ai">AI</div>
  <div class="bar bar-ml">ML</div>
  <div class="bar bar-fm">FM</div>
  <p class="body-copy" style="left:218px;top:62px;width:180px;font-size:9.3px;line-height:18.3px;font-weight:500">A foundational model is a large-scale ML model, trained on vast amounts of data, that serves as the underlying platform for Generative AI (GenAI) to create new and original content.</p>
  <footer class="footer"><span>Copyrights@2025.Company Name.All Rights Reserved</span><span>Page Number: <b>08</b></span></footer>
</section>

</body>
</html>
```